Business Card Design using new attached logo

We are a family run Plumbing and Heating firm looking to improve our company image with an improved business card and new logo.We are looking to keep the company colour (Blue) involved in our design

Reason: New logo added which needs to be incorporated on designs

Industry/Entity Type

Business

Contact Information for Business Card

See attachment of all info required.

Requirements
Must have
• We have just picked a new company logo which is attached.
• Could you please provide your business card designs using this logo.
• We are looking for the logo on the back as well as the front with all the info required

```html
<!DOCTYPE html>
<html lang="en">
<head>
<meta charset="utf-8">
<title>Brightline Services Ltd. – Business Card</title>
<link href="https://fonts.googleapis.com/css2?family=Roboto:wght@400;700&display=swap" rel="stylesheet">
<style>
  :root {
    --page-bg: #ecebe8;
    --sky-blue: #1f8fd8;
    --sky-blue-deep: #1777c2;
    --navy: #2a2373;
    --white: #ffffff;
    --soft-white: #e6e9f5;
  }
  * { margin: 0; padding: 0; box-sizing: border-box; }
  html, body {
    width: 1200px;
    height: 900px;
    overflow: hidden;
    background: var(--page-bg);
    font-family: "Roboto", Arial, sans-serif;
  }
  .canvas {
    position: relative;
    width: 1200px;
    height: 900px;
  }
  .business-card {
    position: absolute;
    left: 100px;
    top: 165px;
    width: 1000px;
    height: 570px;
    overflow: hidden;
    box-shadow: 0 14px 36px rgba(0, 0, 0, 0.22);
    display: flex;
    flex-direction: column;
  }
  .card-top {
    position: relative;
    height: 350px;
    background:
      radial-gradient(ellipse at 45% 30%, rgba(255,255,255,0.10), rgba(255,255,255,0) 60%),
      linear-gradient(160deg, var(--sky-blue) 0%, var(--sky-blue-deep) 100%);
  }
  .card-divider {
    height: 30px;
    background: var(--white);
  }
  .card-bottom {
    flex: 1;
    background: var(--navy);
    padding: 34px 0 0 100px;
    color: var(--soft-white);
    font-size: 31px;
    line-height: 1.33;
    letter-spacing: 0.3px;
  }
  .contact-person {
    position: absolute;
    right: 42px;
    top: 36px;
    text-align: right;
    color: var(--white);
  }
  .contact-person .person-name {
    font-weight: 700;
    font-size: 27px;
    letter-spacing: 0.5px;
  }
  .contact-person .person-role {
    font-weight: 700;
    font-size: 20px;
    margin-top: 6px;
  }
  .contact-person .person-mobile {
    font-size: 24px;
    margin-top: 8px;
  }
  .company-name {
    position: absolute;
    left: 300px;
    top: 108px;
    color: var(--white);
    font-weight: 400;
    text-align: center;
  }
  .company-name .name-main {
    display: block;
    font-size: 78px;
    line-height: 1;
    letter-spacing: 1px;
  }
  .company-name .name-sub {
    display: block;
    font-size: 28px;
    letter-spacing: 7px;
    margin-top: 6px;
  }
</style>
</head>
<body>
<main class="canvas">
  <article class="business-card">
    <section class="card-top">
      <div class="company-name">
        <span class="name-main">Brightline</span>
        <span class="name-sub">Services Ltd.</span>
      </div>
      <div class="contact-person">
        <p class="person-name">MARK DALTON</p>
        <p class="person-role">Director</p>
        <p class="person-mobile">Mob: 07700 900123</p>
      </div>
    </section>
    <div class="card-divider"></div>
    <section class="card-bottom">
      <p class="address">14 Mill Parade, Elm Road, Harton, Surrey HT1 2AB</p>
      <p class="phones">Tel : 020 7946 0321, Fax.: 020 7946 0322</p>
      <p class="email">mark@brightlineservices.co.uk</p>
    </section>
  </article>
</main>
</body>
</html>
```